Local Flower Farm Needs Business Card Design

I need business cards designed for a flower farm based in Eudora, Kansas.
Business Info:
We are a local cut flower farm located in Eudora, Kansas, founded by Corinne Haldwick. What started as a passion for agriculture and search for more joy in daily life has blossomed into a small business dedicated to providing the community with beautiful, fresh, and sustainable flowers. We specialize in local, seasonal blooms, ensuring that every petal reflects the care and dedication we pour into our craft. Our mission is to deliver the highest quality flowers directly to our customers through local farmers markets and to florists who share our commitment to sustainability. Join us in celebrating the beauty of nature, one bloom at a time!
Contact Details:
Corinne Haldwick
Owner
Phone 913-555-0147
Facebook: Rosalind Thorpe Gardens
Instagram: @RosalindThorpeGardens
Website: RosalindThorpeGardens.example
Target Market(s)
Wholesale to Florists and Direct to Consumer via Farmers Market
Industry/Entity Type
Florist, Farm
Contact Information for Business Card
Name, Contact Info, Logo
Look and feel
Each slider illustrates characteristics of the customer's brand and the style your logo design should communicate.

```html
<!DOCTYPE html>
<html lang="en">
<head>
<meta charset="utf-8">
<title>Rosalind Thorpe Gardens – Business Card</title>
<link href="https://fonts.googleapis.com/css2?family=Roboto:wght@400;700&display=swap" rel="stylesheet">
<style>
  :root {
    --backdrop: #2b2d31;
    --teal-deep: #0f3a3f;
    --teal-dark: #0b2f34;
    --teal-accent: #1d6468;
    --paper: #ffffff;
    --ink-light: #ffffff;
    --ink-soft: #d5e3e3;
  }
  html, body {
    margin: 0;
    width: 1200px;
    height: 900px;
    overflow: hidden;
    background: var(--backdrop);
    font-family: "Roboto", Arial, sans-serif;
  }
  .canvas {
    position: relative;
    width: 1200px;
    height: 900px;
  }
  .card {
    position: absolute;
    left: 250px;
    width: 700px;
    height: 400px;
    border-radius: 34px;
    overflow: hidden;
    background: linear-gradient(160deg, var(--teal-deep), var(--teal-dark));
  }
  .card--front { top: 35px; }
  .card--back  { top: 465px; }

  .card__shape {
    position: absolute;
    inset: 0;
    width: 100%;
    height: 100%;
  }

  .brand-seal {
    position: absolute;
    width: 210px;
    height: 210px;
    border-radius: 50%;
    box-sizing: border-box;
    display: flex;
    align-items: center;
    justify-content: center;
    text-align: center;
  }
  .brand-seal__name {
    font-family: "Roboto", Arial, sans-serif;
    font-weight: 400;
    font-size: 21px;
    letter-spacing: 2px;
    line-height: 1.35;
    text-transform: uppercase;
  }
  .card--front .brand-seal {
    left: 48px;
    top: 95px;
    border: 2px solid var(--teal-deep);
  }
  .card--front .brand-seal__name { color: var(--teal-deep); }
  .card--back .brand-seal {
    left: 245px;
    top: 95px;
    border: 2px solid var(--ink-light);
  }
  .card--back .brand-seal__name { color: var(--ink-light); }

  .contact {
    position: absolute;
    left: 395px;
    top: 92px;
    color: var(--ink-light);
  }
  .contact__name {
    margin: 0;
    font-size: 27px;
    font-weight: 700;
    letter-spacing: 0.5px;
    text-transform: uppercase;
  }
  .contact__role {
    margin: 4px 0 0;
    font-size: 16px;
    color: var(--ink-soft);
  }
  .contact__rule {
    width: 12px;
    height: 1px;
    background: var(--ink-soft);
    margin: 10px 0 14px;
  }
  .contact__list {
    list-style: none;
    margin: 0;
    padding: 0;
  }
  .contact__item {
    display: flex;
    align-items: center;
    gap: 8px;
    font-size: 18px;
    line-height: 30px;
  }
  .contact__icon {
    width: 14px;
    height: 14px;
    flex: none;
  }
</style>
</head>
<body>
<main class="canvas">

  <section class="card card--front" aria-label="Business card front">
    <svg class="card__shape" viewBox="0 0 700 400" aria-hidden="true">
      <path d="M0 0 H330 C390 90 395 300 300 400 H0 Z" fill="var(--teal-accent)"/>
      <path d="M0 0 H300 C365 100 360 300 270 400 H0 Z" fill="var(--paper)"/>
    </svg>

    <div class="brand-seal">
      <span class="brand-seal__name">Rosalind<br>Thorpe<br>Gardens</span>
    </div>

    <div class="contact">
      <h1 class="contact__name">Corinne Haldwick</h1>
      <p class="contact__role">Owner</p>
      <div class="contact__rule"></div>
      <ul class="contact__list">
        <li class="contact__item">
          <svg class="contact__icon" viewBox="0 0 24 24" aria-hidden="true">
            <path d="M6.6 10.8a15.1 15.1 0 0 0 6.6 6.6l2.2-2.2a1 1 0 0 1 1-.25 11.4 11.4 0 0 0 3.6.57 1 1 0 0 1 1 1V20a1 1 0 0 1-1 1A17 17 0 0 1 3 4a1 1 0 0 1 1-1h3.5a1 1 0 0 1 1 1c0 1.25.2 2.45.57 3.57a1 1 0 0 1-.25 1z" fill="var(--ink-light)"/>
          </svg>
          (913)555-0147
        </li>
        <li class="contact__item">
          <svg class="contact__icon" viewBox="0 0 24 24" aria-hidden="true"><circle cx="12" cy="12" r="9" fill="var(--ink-light)"/></svg>
          Rosalind Thorpe Gardens
        </li>
        <li class="contact__item">
          <svg class="contact__icon" viewBox="0 0 24 24" aria-hidden="true"><circle cx="12" cy="12" r="9" fill="var(--ink-light)"/></svg>
          @RosalindThorpeGardens
        </li>
        <li class="contact__item">
          <svg class="contact__icon" viewBox="0 0 24 24" aria-hidden="true"><circle cx="12" cy="12" r="9" fill="var(--ink-light)"/></svg>
          RosalindThorpeGardens.example
        </li>
      </ul>
    </div>
  </section>

  <section class="card card--back" aria-label="Business card back">
    <div class="brand-seal">
      <span class="brand-seal__name">Rosalind<br>Thorpe<br>Gardens</span>
    </div>
  </section>

</main>
</body>
</html>
```